Expedition Cruise Sales Website for the Polar Regions (Antarctica & Arctic)

This will be a website for selling cruises.
This site should have a homepage, a ship page, destinations, and itineraries.
I have created a file specifying each page, and it is attached.
Pages:
1. Home
2. Cruise Lines
- 2.1 Ships
3. Destinations
- 3.1 Region - 3.2 Country - 3.3 City
4. Itineraries
- 4.1 Itinerary
5. Blog / Travel Tips 6. About Us
7. Contact
Please take a look on the attached pdf
Target Market(s)
Expedition Travelers
Coding
Coded - Design and coding required
Number of Pages Required
5+ page
Font styles to use
Look and feel
Each slider illustrates characteristics of the customer's brand and the style your logo design should communicate.

```html
<!DOCTYPE html>
<html lang="en">
<head>
<meta charset="utf-8">
<title>Polarvia.co – Luxury Cruises</title>
<link href="https://fonts.googleapis.com/css2?family=Poppins:ital,wght@0,400;0,500;0,600;0,700;0,800;0,900;1,400&display=swap" rel="stylesheet">
<style>
:root{
  --ink:#111111;
  --text:#2b2b2b;
  --muted:#8a8f99;
  --line:#e6e8ee;
  --field:#f2f4fb;
  --brand:#3b7bc4;
  --blue:#2f6fd6;
  --star:#f07a2a;
  --white:#ffffff;
  --footer:#151515;
}
*{box-sizing:border-box;margin:0;padding:0}
html,body{width:1200px;height:3793px;overflow:hidden}
body{position:relative;background:var(--white);font-family:'Poppins',sans-serif;color:var(--text)}
.abs{position:absolute}
svg{display:block}

/* header */
.logo{display:flex;align-items:center;gap:6px;font-weight:600;font-size:15px;color:var(--brand);white-space:nowrap}
.logo-dot{width:10px;height:10px;border-radius:50%;background:var(--brand)}
.nav{left:136px;top:52px;display:flex;gap:35px;font-size:14px;color:var(--ink)}
.nav .active{font-weight:600}
.btn-dark{background:var(--ink);color:var(--white);border-radius:40px;display:flex;align-items:center;justify-content:center;font-size:13px;font-weight:500;white-space:nowrap}
.search{left:22px;top:116px;width:576px;height:39px;border-radius:20px;background:var(--field);display:flex;align-items:center;gap:12px;padding-left:24px;font-size:10.5px;color:var(--ink)}
.pill{top:116px;height:39px;border-radius:20px;background:var(--field);display:flex;align-items:center;justify-content:center;gap:8px;font-size:10.5px;color:var(--ink)}
.pill.on{background:var(--ink);color:var(--white)}

/* hero */
.hero{left:21px;top:191px;width:1157px;height:575px;border-radius:30px;overflow:hidden;
  background:linear-gradient(180deg,#a9b6c7 0%,#8e9db0 35%,#6f8092 60%,#5a6b7e 100%)}
.hero .ship{position:absolute;left:300px;top:40px;width:560px;height:470px;border-radius:40% 40% 10% 10%;
  background:radial-gradient(ellipse at 50% 60%,rgba(240,240,240,.55),rgba(120,130,145,0) 70%)}
.hero-top{left:63px;top:26px;width:1031px;display:flex;align-items:center;gap:14px;color:var(--white);font-size:12px}
.hero-top .rule{flex:1;height:2px;background:rgba(255,255,255,.85)}
.hero h1{left:0;top:210px;width:1157px;text-align:center;font-size:86px;font-weight:800;color:var(--white);letter-spacing:1px;line-height:1}
.hero p{left:0;top:313px;width:1157px;text-align:center;font-size:14px;color:var(--white)}
.hero .cta{left:463px;top:377px;width:230px;height:45px;font-size:13.5px;font-weight:600}

.booking{left:69px;top:704px;width:1060px;height:110px;background:var(--white);border-radius:8px;box-shadow:0 6px 24px rgba(20,30,60,.08)}
.booking .label{font-size:10px;color:var(--muted)}
.booking .field{height:40px;width:256px;background:var(--field);border-radius:4px;display:flex;align-items:center;gap:12px;padding:0 22px;font-size:10.5px;color:var(--ink)}

/* sections */
.sec-title{left:0;width:1200px;text-align:center;font-size:30px;font-weight:800;color:var(--ink)}
.sec-sub{left:300px;width:600px;text-align:center;font-size:11.5px;line-height:17.5px;color:var(--ink)}
.card{width:320px;background:var(--white);border-radius:6px;box-shadow:0 4px 18px rgba(20,30,60,.07);overflow:hidden}
.card .img{height:212px}
.card .body{padding:0 17px}
.card h3{font-size:20px;font-weight:500;color:var(--ink);display:flex;justify-content:space-between;align-items:center;white-space:nowrap}
.card h3 small{font-size:11px;font-weight:400;color:#555;display:flex;align-items:center;gap:4px}
.card .rule{height:1px;background:var(--line);margin-top:14px}
.stats{display:flex;justify-content:space-between;font-size:10.5px;color:var(--muted);margin-top:14px}
.stats span{display:flex;align-items:center;gap:5px}
.card .desc{font-size:11.5px;line-height:18px;color:var(--ink);margin-top:23px;height:36px;overflow:hidden;display:-webkit-box;-webkit-line-clamp:2;-webkit-box-orient:vertical}
.card .foot{display:flex;justify-content:space-between;align-items:center;margin-top:12px}
.price{font-size:20px;font-weight:600;color:var(--ink)}
.card .btn-dark{width:122px;height:37px;font-size:11.5px}

/* testimonials */
.t-title{left:100px;top:2250px;font-size:29px;font-weight:800;color:var(--ink)}
.t-sub{left:707px;top:2242px;width:394px;font-size:11.5px;line-height:17.5px;color:var(--ink);text-align:justify}
.t-card{top:2348px;height:332px;background:var(--white);border-radius:6px;box-shadow:0 4px 18px rgba(20,30,60,.07)}
.quote{font-style:italic;font-size:13px;line-height:20px;color:#333;text-align:justify}
.circle-btn{width:36px;height:36px;border-radius:50%;display:flex;align-items:center;justify-content:center}
.circle-btn.light{background:#f1f2f5}
.circle-btn.blue{background:var(--blue)}

/* newsletter */
.news{left:0;top:2790px;width:1200px;height:552px;
  background:linear-gradient(180deg,#cbd6e2 0%,#aebdcd 30%,#5e7186 60%,#3f5670 78%,#4f6f92 100%)}
.news h2{left:0;top:148px;width:1200px;text-align:center;color:var(--white);font-size:37px;font-weight:800}
.news p{left:320px;top:215px;width:560px;text-align:center;color:var(--white);font-size:11.5px;line-height:17.5px}
.news .email{left:389px;top:286px;width:421px;height:38px;background:var(--white);border-radius:20px;font-size:10.5px;color:var(--ink);display:flex;align-items:center;padding-left:20px}
.btn-white{background:var(--white);color:var(--ink);border-radius:20px;display:flex;align-items:center;justify-content:center;font-size:12px;font-weight:500}

/* footer */
.footer{left:0;top:3342px;width:1200px;height:451px;background:var(--footer);color:var(--white)}
.footer .about{left:99px;top:181px;width:276px;font-size:11.5px;line-height:18.5px;color:#a9a9a9;text-align:justify}
.fcol{top:90px;font-size:13px}
.fcol h4{font-size:14.5px;font-weight:600;margin-bottom:15px;color:var(--white)}
.fcol a{display:block;color:#a9a9a9;text-decoration:none;margin-bottom:15px}
.footer .divider{left:99px;top:351px;width:1001px;height:1px;background:#333}
.footer .copy{top:394px;font-size:13px;color:#cfcfcf}
</style>
</head>
<body>

<!-- header -->
<div class="abs logo" style="left:20px;top:54px"><span class="logo-dot"></span>Polarvia.co</div>
<nav class="abs nav">
  <span class="active">Home</span><span>Cruise Lines</span><span>Destinations</span><span>Itineraries</span><span>Blog</span><span>About Us</span>
</nav>
<div class="abs btn-dark" style="left:1051px;top:41px;width:122px;height:40px;font-size:14px">Contact</div>

<div class="abs search">
  <svg width="12" height="12" viewBox="0 0 12 12"><circle cx="5" cy="5" r="3.8" fill="none" stroke="#111" stroke-width="1.3"/><path d="M8 8l3 3" stroke="#111" stroke-width="1.3"/></svg>
  Search Cruise Destination
</div>
<div class="abs pill on" style="left:624px;width:134px"><svg width="16" height="16" viewBox="0 0 16 16"><circle cx="8" cy="8" r="8" fill="#fff"/><path d="M5 11h6M6 10V6l2-2 2 2v4" stroke="#111" stroke-width="1.2" fill="none"/></svg>Departure date</div>
<div class="abs pill" style="left:779px;width:118px"><svg width="10" height="10" viewBox="0 0 10 10"><path d="M1 9h8M2.5 8V4L5 1.5 7.5 4v4" stroke="#111" stroke-width="1.1" fill="none"/></svg>Cruise Length</div>
<div class="abs pill" style="left:919px;width:118px"><svg width="10" height="10" viewBox="0 0 10 10"><path d="M1 9h8M2.5 8V4L5 1.5 7.5 4v4" stroke="#111" stroke-width="1.1" fill="none"/></svg>Departure port</div>
<div class="abs pill" style="left:1057px;width:118px"><svg width="10" height="10" viewBox="0 0 10 10"><path d="M1 9h8M2.5 8V4L5 1.5 7.5 4v4" stroke="#111" stroke-width="1.1" fill="none"/></svg>Cruise Line</div>

<!-- hero -->
<section class="abs hero">
  <div class="ship" role="img" aria-label="Large white cruise ship sailing toward the viewer on calm sea under an overcast sky"></div>
  <div class="abs hero-top"><span>Special Offers Available!</span><span class="rule"></span><span>January 2025 - April 2025</span></div>
  <h1 class="abs">LUXURY AWAITS YOU</h1>
  <p class="abs">Explore the world's best destinations aboard the finest ships. Book your dream cruise today.</p>
  <div class="abs btn-dark cta">Start Your Journey</div>
</section>

<div class="abs booking">
  <div class="abs label" style="left:27px;top:22px">Cruising to</div>
  <div class="abs field" style="left:27px;top:44px"><svg width="14" height="14" viewBox="0 0 14 14"><path d="M1 13h12M3 12V6l4-4 4 4v6M6 12V9h2v3" stroke="#111" stroke-width="1.1" fill="none"/></svg>Anywhere</div>
  <div class="abs label" style="left:323px;top:22px">Date</div>
  <div class="abs field" style="left:323px;top:44px"><svg width="16" height="16" viewBox="0 0 16 16"><rect x="1.5" y="2.5" width="13" height="12" rx="1.5" fill="none" stroke="#111" stroke-width="1.1"/><path d="M1.5 6h13M5 1v3M11 1v3" stroke="#111" stroke-width="1.1"/></svg>Select Date</div>
  <div class="abs label" style="left:617px;top:22px">Guest</div>
  <div class="abs field" style="left:617px;top:44px"><svg width="16" height="14" viewBox="0 0 16 14"><circle cx="6" cy="4" r="2.6" fill="none" stroke="#111" stroke-width="1.2"/><path d="M1 12c0-3 2-4.5 5-4.5s5 1.5 5 4.5" fill="none" stroke="#111" stroke-width="1.2"/><circle cx="11.5" cy="4.5" r="2" fill="none" stroke="#111" stroke-width="1.1"/></svg>Select Guest<svg style="margin-left:auto" width="8" height="5" viewBox="0 0 8 5"><path d="M0 0h8L4 5z" fill="#111"/></svg></div>
  <div class="abs btn-dark" style="left:912px;top:32px;width:122px;height:37px;font-size:11.5px">Search Cruise</div>
</div>

<!-- deals -->
<h2 class="abs sec-title" style="top:918px">UNBEATABLE CRUISE DEALS</h2>
<p class="abs sec-sub" style="top:969px">Discover Exclusive Offers And Embark On A Luxurious Adventure Without Breaking The Bank. Check Out Our Best Deals Below And Set Sail On The Journey Of A Lifetime.</p>

<article class="abs card" style="left:100px;top:1040px;height:444px">
  <div class="img" role="img" aria-label="Expedition ship among Antarctic ice and snowy mountains" style="background:linear-gradient(180deg,#c9d0d8,#8b959f 55%,#5f6a74)"></div>
  <div class="body">
    <h3 style="margin-top:17px">Best Antarctic Cruises<small><svg width="11" height="11" viewBox="0 0 10 10"><path d="M5 0l1.5 3.3 3.5.4-2.6 2.3.8 3.5L5 7.7 1.8 9.5l.8-3.5L0 3.7l3.5-.4z" fill="#222"/></svg>4.8</small></h3>
    <div class="rule"></div>
    <div class="stats">
      <span><svg width="11" height="11" viewBox="0 0 11 11"><path d="M2 0v9h9M0 2h9v9" fill="none" stroke="#3b5a9c" stroke-width="1.1"/></svg>85" ft</span>
      <span><svg width="13" height="11" viewBox="0 0 13 11"><circle cx="5" cy="3" r="2.2" fill="none" stroke="#3b5a9c" stroke-width="1.1"/><path d="M1 10c0-2.5 1.6-3.8 4-3.8S9 7.5 9 10M9 1.2a2 2 0 010 3.8M10.5 6.5c1 .5 1.7 1.6 1.7 3.5" fill="none" stroke="#3b5a9c" stroke-width="1.1"/></svg>6 Guest</span>
      <span><svg width="11" height="11" viewBox="0 0 11 11"><circle cx="5.5" cy="5.5" r="4.8" fill="none" stroke="#3b5a9c" stroke-width="1.1"/><path d="M3.5 6.5c.6.9 1.2 1.2 2 1.2s1.4-.3 2-1.2" fill="none" stroke="#3b5a9c" stroke-width="1"/></svg>5 Crew</span>
    </div>
    <p class="desc">Experience the untouched beauty of Antarctica. Navigate through massive glaciers and iceberg fields with expert guides.</p>
    <div class="foot"><span class="price">$4,499</span><span class="btn-dark">Book Now</span></div>
  </div>
</article>
<article class="abs card" style="left:440px;top:1040px;height:444px">
  <div class="img" role="img" aria-label="Cruise ship in turquoise tropical water beside palm trees" style="background:linear-gradient(180deg,#2f8a6a,#27b3c4 45%,#1f9fb0)"></div>
  <div class="body">
    <h3 style="margin-top:17px">Top Galápagos Cruises<small><svg width="11" height="11" viewBox="0 0 10 10"><path d="M5 0l1.5 3.3 3.5.4-2.6 2.3.8 3.5L5 7.7 1.8 9.5l.8-3.5L0 3.7l3.5-.4z" fill="#222"/></svg>4.8</small></h3>
    <div class="rule"></div>
    <div class="stats">
      <span><svg width="11" height="11" viewBox="0 0 11 11"><path d="M2 0v9h9M0 2h9v9" fill="none" stroke="#3b5a9c" stroke-width="1.1"/></svg>85" ft</span>
      <span><svg width="13" height="11" viewBox="0 0 13 11"><circle cx="5" cy="3" r="2.2" fill="none" stroke="#3b5a9c" stroke-width="1.1"/><path d="M1 10c0-2.5 1.6-3.8 4-3.8S9 7.5 9 10M9 1.2a2 2 0 010 3.8M10.5 6.5c1 .5 1.7 1.6 1.7 3.5" fill="none" stroke="#3b5a9c" stroke-width="1.1"/></svg>6 Guest</span>
      <span><svg width="11" height="11" viewBox="0 0 11 11"><circle cx="5.5" cy="5.5" r="4.8" fill="none" stroke="#3b5a9c" stroke-width="1.1"/><path d="M3.5 6.5c.6.9 1.2 1.2 2 1.2s1.4-.3 2-1.2" fill="none" stroke="#3b5a9c" stroke-width="1"/></svg>5 Crew</span>
    </div>
    <p class="desc">Discover nature's masterpiece with a luxury cruise to the Galápagos Islands. Explore rare wildlife and volcanic shores.</p>
    <div class="foot"><span class="price">$2,999</span><span class="btn-dark">Book Now</span></div>
  </div>
</article>
<article class="abs card" style="left:780px;top:1040px;height:444px">
  <div class="img" role="img" aria-label="White cruise ship docked beside a wooden pier under blue sky" style="background:linear-gradient(180deg,#6ba8e0,#b9d6ee 50%,#7a6a5c)"></div>
  <div class="body">
    <h3 style="margin-top:17px">Last-Minute Deals</h3>
    <div class="rule"></div>
    <div class="stats">
      <span><svg width="11" height="11" viewBox="0 0 11 11"><path d="M2 0v9h9M0 2h9v9" fill="none" stroke="#3b5a9c" stroke-width="1.1"/></svg>85" ft</span>
      <span><svg width="13" height="11" viewBox="0 0 13 11"><circle cx="5" cy="3" r="2.2" fill="none" stroke="#3b5a9c" stroke-width="1.1"/><path d="M1 10c0-2.5 1.6-3.8 4-3.8S9 7.5 9 10M9 1.2a2 2 0 010 3.8M10.5 6.5c1 .5 1.7 1.6 1.7 3.5" fill="none" stroke="#3b5a9c" stroke-width="1.1"/></svg>6 Guest</span>
      <span><svg width="11" height="11" viewBox="0 0 11 11"><circle cx="5.5" cy="5.5" r="4.8" fill="none" stroke="#3b5a9c" stroke-width="1.1"/><path d="M3.5 6.5c.6.9 1.2 1.2 2 1.2s1.4-.3 2-1.2" fill="none" stroke="#3b5a9c" stroke-width="1"/></svg>5 Crew</span>
    </div>
    <p class="desc">Don't miss out! Book your next adventure at a discounted rate with our exclusive last-minute departures.</p>
    <div class="foot"><span class="price">$1,889</span><span class="btn-dark">Grab the Deal</span></div>
  </div>
</article>

<!-- cruise lines -->
<h2 class="abs sec-title" style="top:1586px">CRUISE WITH THE BEST IN THE BUSINESS</h2>
<p class="abs sec-sub" style="top:1639px">Choose From Our Premium Cruise Lines For A Top-Tier Experience. Whether You're Seeking Luxury, Adventure, Or Relaxation, We Have The Right Cruise For You.</p>

<article class="abs card" style="left:100px;top:1709px;height:399px">
  <div class="img" role="img" aria-label="Large cruise ship at a harbor quay under blue sky" style="background:linear-gradient(180deg,#3d7fc4,#a9c9e6 50%,#d8dde2)"></div>
  <div class="body">
    <h3 style="margin-top:22px">Meridian Seas</h3>
    <p class="desc" style="margin-top:17px">Known for groundbreaking ships and exceptional service, Meridian Seas offers unmatched luxury at sea.</p>
    <span class="btn-dark" style="width:122px;height:37px;font-size:11.5px;margin-top:10px">Learn More</span>
  </div>
</article>
<article class="abs card" style="left:440px;top:1709px;height:399px">
  <div class="img" role="img" aria-label="Two travelers relaxing on a sunny deck with palm trees and a ship behind" style="background:linear-gradient(180deg,#c9d9e6,#e9dcc8 55%,#b08a5c)"></div>
  <div class="body">
    <h3 style="margin-top:22px">Aurora Voyages</h3>
    <p class="desc" style="margin-top:17px">Elevate your cruise experience with Aurora Voyages, offering modern luxury and impeccable service throughout.</p>
    <span class="btn-dark" style="width:122px;height:37px;font-size:11.5px;margin-top:10px">Learn More</span>
  </div>
</article>
<article class="abs card" style="left:780px;top:1709px;height:399px">
  <div class="img" role="img" aria-label="Aerial view of several cruise ships docked at a tropical port" style="background:linear-gradient(160deg,#1f76b8,#3fa9c8 50%,#8fd3d8)"></div>
  <div class="body">
    <h3 style="margin-top:22px">Halcyon Tide Cruises</h3>
    <p class="desc" style="margin-top:17px">Known for groundbreaking ships and exceptional service, Halcyon Tide offers unmatched luxury at sea.</p>
    <span class="btn-dark" style="width:122px;height:37px;font-size:11.5px;margin-top:10px">Learn More</span>
  </div>
</article>

<!-- testimonials -->
<h2 class="abs t-title">WHAT OUR GUESTS ARE SAYING</h2>
<p class="abs t-sub">Our Passengers Don't Just Go On Cruises—They Experience The Trip Of A Lifetime. See Our Passengers Don't Just Go On Cruises—They Embark On Extraordinary Journeys That Leave Lasting Memories.</p>

<div class="abs t-card" style="left:100px;width:504px">
  <svg class="abs" style="left:37px;top:33px" width="34" height="28" viewBox="0 0 34 28"><path d="M0 28V12C0 5 4 1 12 0v6c-3 1-5 3-5 6h5v16zM20 28V12c0-7 4-11 12-12v6c-3 1-5 3-5 6h5v16z" fill="var(--blue)"/></svg>
  <p class="abs quote" style="left:37px;top:80px;width:425px">The Mediterranean cruise was everything I dreamed of and more. We visited some of the most beautiful ports, and the luxurious accommodations made it feel like a five-star resort on the water. The staff went above and beyond to make every moment special. I've already booked my next cruise!</p>
  <svg class="abs" style="left:443px;top:190px" width="34" height="28" viewBox="0 0 34 28"><path d="M14 0v16c0 7-4 11-12 12v-6c3-1 5-3 5-6H2V0zM34 0v16c0 7-4 11-12 12v-6c3-1 5-3 5-6h-5V0z" fill="var(--blue)"/></svg>
  <div class="abs" style="left:32px;top:231px;width:48px;height:48px;border-radius:50%;background:linear-gradient(135deg,#d9c3ae,#7b6a60)" role="img" aria-label="Guest portrait"></div>
  <div class="abs" style="left:95px;top:234px;font-size:15px;font-weight:500;color:var(--ink)">Lena M</div>
  <div class="abs" style="left:95px;top:256px;font-size:11.5px;font-style:italic;color:#444">Verified Traveler</div>
  <svg class="abs" style="left:93px;top:280px" width="98" height="16" viewBox="0 0 98 16"><g fill="var(--star)"><path id="s" d="M8 0l2.3 5 5.3.6-4 3.6 1.2 5.3L8 11.8 3.2 14.5l1.2-5.3-4-3.6L5.7 5z"/><use href="#s" x="20.5"/><use href="#s" x="41"/><use href="#s" x="61.5"/><use href="#s" x="82"/></g></svg>
  <div class="abs circle-btn light" style="left:387px;top:244px"><svg width="8" height="12" viewBox="0 0 8 12"><path d="M6 1L1 6l5 5" stroke="#555" stroke-width="1.4" fill="none"/></svg></div>
  <div class="abs circle-btn blue" style="left:437px;top:244px"><svg width="8" height="12" viewBox="0 0 8 12"><path d="M2 1l5 5-5 5" stroke="#fff" stroke-width="1.6" fill="none"/></svg></div>
</div>

<div class="abs t-card" style="left:618px;width:480px">
  <div class="abs" style="left:30px;top:27px;width:421px;height:194px;background:linear-gradient(180deg,#b8cfe6,#dde6ee 60%,#8a7a68)" role="img" aria-label="Traveler standing on a sailboat deck by the mast on a sunny day"></div>
  <div class="abs circle-btn light" style="left:30px;top:255px"><svg width="8" height="12" viewBox="0 0 8 12"><path d="M6 1L1 6l5 5" stroke="#555" stroke-width="1.4" fill="none"/></svg></div>
  <div class="abs" style="left:84px;top:243px;width:59px;height:59px;border-radius:4px;background:linear-gradient(180deg,#c9d6e2,#8c7e70)" role="img" aria-label="Gallery thumbnail of traveler on deck"></div>
  <div class="abs" style="left:161px;top:243px;width:59px;height:59px;border-radius:4px;background:linear-gradient(180deg,#4d3c34,#a89888)" role="img" aria-label="Gallery thumbnail of traveler portrait"></div>
  <div class="abs" style="left:239px;top:243px;width:59px;height:59px;border-radius:4px;background:linear-gradient(180deg,#bcd0e3,#ece9e4)" role="img" aria-label="Gallery thumbnail of traveler at sea"></div>
  <div class="abs" style="left:317px;top:243px;width:59px;height:59px;border-radius:4px;background:linear-gradient(180deg,#cfdbe6,#e8e4de)" role="img" aria-label="Gallery thumbnail of traveler by the mast"></div>
  <div class="abs circle-btn blue" style="left:393px;top:255px"><svg width="8" height="12" viewBox="0 0 8 12"><path d="M2 1l5 5-5 5" stroke="#fff" stroke-width="1.6" fill="none"/></svg></div>
</div>

<!-- newsletter -->
<section class="abs news" role="img" aria-label="City skyline by the water with a cruise ship in the harbor">
  <h2 class="abs">STAY UPDATED WITH THE LATEST CRUISE DEALS</h2>
  <p class="abs">Sign Up For Our Newsletter To Receive Exclusive Offers, The Latest News, And Helpful Travel Tips Straight To Your Inbox. Plus, Get The Option To Contact Us Instantly Via Chat.</p>
  <div class="abs email">Enter Your Email</div>
  <div class="abs btn-white" style="left:448px;top:364px;width:147px;height:38px">Subscribe Now</div>
  <div class="abs btn-dark" style="left:607px;top:364px;width:144px;height:38px;font-size:11px;gap:8px"><svg width="16" height="16" viewBox="0 0 16 16"><circle cx="8" cy="8" r="6.5" fill="none" stroke="#fff" stroke-width="1.3"/></svg>Chat Me</div>
</section>

<!-- footer -->
<footer class="abs footer">
  <div class="abs logo" style="left:99px;top:129px;color:var(--white)"><span class="logo-dot" style="background:var(--white)"></span>Polarvia.co</div>
  <p class="abs about">We are a luxury cruise company offering unforgettable voyages to the world's most exclusive destinations. With over 20 years of experience, we provide exceptional service, comfort, and adventure on every journey.</p>
  <div class="abs fcol" style="left:665px"><h4>Community</h4><a>Events</a><a>Blogs</a><a>Best Deal</a><a>Forum</a><a>Invite Friend</a></div>
  <div class="abs fcol" style="left:829px"><h4>Community</h4><a>Home</a><a>Cruise Lines</a><a>Destinations</a><a>Itineraries</a><a>Blog</a></div>
  <div class="abs fcol" style="left:992px"><h4>Useful Link</h4><a>Upcoming Event</a><a>Book A Ticket</a><a>Travel with Us</a></div>
  <div class="abs divider"></div>
  <div class="abs copy" style="left:99px">Copyright © 2025 Polarvia.co</div>
  <div class="abs copy" style="left:928px">All rights reserved.</div>
</footer>

</body>
</html>
```